Travel Agency Website - Simple General

Need a 7 page simple design that is pretty repetitive. Need to be able to load quickly that is SEO optimized. Trying to give ideas on what they can do, be personal as we are local, but at the same time come across as professional and get information easily with little burden.

- Landing Page
- Brimwell Vacations Page
- Family Trips
- Road Trips from Texas
- Other Destinations
- About Us Page
- Contact Us Page

Target Market(s)

Families

Coding

Coded - Design and coding required

Number of Pages Required

5+ page

Colors

Designer to choose colors to be used in the design.

Requirements
Must have
• Like it to flow easily with our logo. Use that for colors, etc.

```html
<!DOCTYPE html>
<html lang="en">
<head>
<meta charset="utf-8">
<title>Roam Together Travel Co. — Family Travel from Texas</title>
<meta name="description" content="Locally owned family travel planning: Brimwell vacations, family trips, Texas road trips and more.">
<link href="https://fonts.googleapis.com/css2?family=Outfit:wght@400;500;600;700&family=Allura&display=swap" rel="stylesheet">
<style>
:root{
  --teal:#1d5862;
  --teal-dark:#163d44;
  --gold:#c4904a;
  --cream:#fdf1e3;
  --ink:#1f2b2e;
  --muted:#4b5659;
  --line:#e4e0da;
  --white:#ffffff;
}
*{box-sizing:border-box;margin:0;padding:0}
html,body{width:1200px;height:5106px;overflow:hidden}
body{font-family:'Outfit',sans-serif;color:var(--ink);background:var(--white);position:relative}
.abs{position:absolute}
.script{font-family:'Allura',cursive;color:var(--gold);font-weight:400}
.section-head{position:absolute;left:0;width:1200px;text-align:center}
.section-head .script{font-size:40px;line-height:1}
.section-head h2{font-size:34px;font-weight:600;color:var(--teal);line-height:1.1}
.section-head .rule{width:64px;height:3px;background:var(--gold);margin:12px auto 0}
.section-head p{font-size:13px;color:var(--muted);margin-top:16px}
.pill{display:inline-flex;align-items:center;gap:12px;background:var(--gold);color:var(--white);border-radius:30px;font-size:12px;font-weight:600;letter-spacing:.4px;padding:6px 6px 6px 18px;height:40px;text-transform:uppercase}
.pill .arrow{width:30px;height:30px;border-radius:50%;background:var(--white);display:flex;align-items:center;justify-content:center}
.photo{position:absolute;overflow:hidden}

/* hero */
.hero{position:absolute;left:0;top:0;width:1200px;height:604px;background:linear-gradient(180deg,#3b6d86 0%,#7fa6b8 38%,#b9c7c4 58%,#d8c7a6 78%,#e6d3b0 100%)}
.brand{position:absolute;left:140px;top:18px;width:118px;height:100px;border-radius:50%;background:var(--white);display:flex;align-items:center;justify-content:center;text-align:center;color:var(--teal);font-size:14px;font-weight:600;line-height:1.15}
.nav{position:absolute;top:32px;left:404px;display:flex;gap:20px;align-items:center;font-size:12px;color:var(--white);text-transform:uppercase}
.nav .pill{margin-left:6px;height:42px}
.hero-copy{position:absolute;left:142px;top:200px;color:var(--white)}
.hero-copy .script{color:var(--white);font-size:54px;line-height:1}
.hero-copy h1{font-size:54px;font-weight:600;line-height:1.05;margin-top:4px}
.hero-copy h1 .script{font-size:62px}
.hero-copy p{font-size:13px;width:450px;margin-top:8px;line-height:1.4}
.hero-copy .pill{margin-top:28px}

/* cards */
.trip-card{position:absolute;width:212px;border-radius:18px;overflow:hidden;color:var(--white)}
.trip-card .cap{position:absolute;left:14px;bottom:16px}
.trip-card .cap b{display:block;font-size:15px;font-weight:500}
.trip-card .cap span{font-size:10px;text-transform:uppercase}
.trip-card .go{position:absolute;right:12px;bottom:14px;width:28px;height:28px;border:1.5px solid var(--white);border-radius:50%;display:flex;align-items:center;justify-content:center}

/* texas band */
.texas-panel{position:absolute;left:648px;top:1224px;width:552px;height:364px;background:var(--teal);border-bottom-left-radius:120px;color:var(--white);padding:52px 0 0 60px}
.texas-panel .script{color:var(--white);font-size:36px}
.texas-panel h2{font-size:34px;font-weight:500;line-height:1.15}
.texas-panel p{font-size:12px;width:360px;margin-top:8px;line-height:1.35}
.texas-panel .pill{margin-top:24px}

/* about */
.about-copy{position:absolute;left:142px;top:1790px;width:380px}
.about-copy .script{font-size:36px}
.about-copy h2{font-size:34px;font-weight:600;color:var(--teal);line-height:1.1}
.about-copy .rule{width:64px;height:3px;background:var(--gold);margin:14px 0 18px}
.about-copy p{font-size:13px;line-height:1.7;margin-bottom:8px}
.about-copy .pill{margin-top:22px}
.badge{position:absolute;left:892px;top:2034px;width:168px;height:156px;background:var(--teal);border-radius:24px 24px 24px 0;color:var(--white);text-align:center;padding-top:24px}
.badge b{font-size:56px;font-weight:600;line-height:1}
.badge span{display:block;font-size:16px;font-weight:600;line-height:1.2;margin-top:4px}

/* why */
.why{position:absolute;left:0;top:2290px;width:1200px;height:740px;background:linear-gradient(180deg,#ffffff 0%,#ffffff 40%,#e3e7e6 58%,#a9b4b0 72%,#4f6a55 86%,#2f4a36 100%)}
.feature{position:absolute;width:206px;height:206px;border-radius:50%;border:2px dotted #7d8c8d;display:flex;align-items:center;justify-content:center}
.feature .disc{width:180px;height:180px;border-radius:50%;background:#f5f1ea;display:flex;flex-direction:column;align-items:center;justify-content:center;text-align:center;font-size:15px;font-weight:600;line-height:1.2;gap:8px}

/* testimonials */
.review{position:absolute;width:324px;height:160px;background:var(--white);border-radius:6px;box-shadow:0 4px 18px rgba(0,0,0,.08);padding:22px 24px}
.review .who{display:flex;gap:10px;align-items:center}
.review .av{width:32px;height:32px;border-radius:50%;color:var(--white);display:flex;align-items:center;justify-content:center;font-size:15px}
.review .name{font-size:14px;font-weight:500}
.review .stars{color:var(--gold);font-size:10px;letter-spacing:2px}
.review .q{position:absolute;right:20px;top:14px;font-size:38px;color:#c9b79a;font-family:Georgia,serif;line-height:1}
.review p{font-size:11px;line-height:1.6;margin-top:18px;color:var(--muted)}
.dots{position:absolute;top:3624px;left:568px;display:flex;gap:14px;align-items:center}
.dots i{width:4px;height:4px;border-radius:50%;background:#999}
.dots i.on{width:12px;height:12px;border:2px solid var(--gold);background:none}

/* inquiry */
.inquiry{position:absolute;left:0;top:3722px;width:1200px;height:594px;background:var(--cream)}
.field{position:absolute;background:var(--white);border:1px solid var(--line);height:52px;display:flex;align-items:center;font-size:11px;color:#8a8f90;padding-left:18px;gap:14px}
.field .sep{width:1px;height:20px;background:var(--line)}
.submit{position:absolute;left:292px;top:4212px;width:616px;height:52px;background:var(--gold);color:var(--white);display:flex;align-items:center;justify-content:center;font-size:12px;font-weight:600;text-transform:uppercase}

/* subscribe */
.sub-box{position:absolute;left:282px;top:4602px;width:636px;height:56px;border:1px solid #c9a46d;border-radius:30px;display:flex;align-items:center;padding-left:22px;font-size:14px;color:#8a8f90}
.sub-box .pill{position:absolute;right:4px;top:4px;background:var(--teal);height:46px;padding-left:22px}

/* footer */
.footer{position:absolute;left:0;top:4716px;width:1200px;height:390px;background:var(--teal-dark);color:var(--white)}
.footer h4{font-size:16px;font-weight:500;text-transform:uppercase;margin-bottom:10px}
.footer li{list-style:none;font-size:13px;line-height:27px}
.contact-row{display:flex;gap:10px;font-size:12px;line-height:1.5;margin-bottom:14px}
.social li{display:flex;align-items:center;gap:10px;line-height:1;margin-bottom:14px}
.social .dot{width:26px;height:26px;border-radius:50%;border:1px solid var(--white)}
.footer .copy{position:absolute;top:362px;width:1200px;text-align:center;font-size:11px}
.footer-brand{position:absolute;left:826px;top:90px;width:234px;height:200px;border-radius:50%;background:var(--white);color:var(--teal);display:flex;align-items:center;justify-content:center;text-align:center;font-size:24px;font-weight:600;line-height:1.15}
</style>
</head>
<body>

<!-- Hero -->
<header class="hero" role="img" aria-label="Photo of a smiling family walking hand in hand along a sunny beach">
  <div class="brand">Roam<br>Together<br>Travel Co.</div>
  <nav class="nav" aria-label="Main">
    <span>Home</span><span>Brimwell</span><span>Family Trips</span><span>Road Trips</span><span>Destinations</span><span>About Us</span>
    <span class="pill">Contact Us <span class="arrow"><svg width="16" height="10" viewBox="0 0 16 10"><path d="M1 5h13M10 1l4 4-4 4" fill="none" stroke="#c4904a" stroke-width="1.6"/></svg></span></span>
  </nav>
  <div class="hero-copy">
    <div class="script">Adventure Start</div>
    <h1>Your Family<br>Adventure <span class="script">Awaits</span></h1>
    <p>Experience unforgettable moments with Roam Together. From Brimwell magic to Texas backroads, we craft perfect family vacations.</p>
    <span class="pill">Start Planning Now <span class="arrow"><svg width="16" height="10" viewBox="0 0 16 10"><path d="M1 5h13M10 1l4 4-4 4" fill="none" stroke="#c4904a" stroke-width="1.6"/></svg></span></span>
  </div>
</header>

<!-- Begin Your Journey -->
<section>
  <div class="section-head" style="top:668px">
    <div class="script">Whist</div>
    <h2>Begin Your Journey.</h2>
    <div class="rule"></div>
    <p>Curated adventures for every family rhythm</p>
  </div>
  <article class="trip-card" style="left:140px;top:832px;height:318px;background:linear-gradient(180deg,#8fb8d0,#c6ad93 60%,#5c4b3c)" role="img" aria-label="Photo of a family relaxing on a boat deck at sea">
    <div class="cap"><b>Brimwell Vacations</b><span>Land and Sea</span></div>
    <span class="go"><svg width="10" height="10" viewBox="0 0 10 10"><path d="M2 8L8 2M3 2h5v5" fill="none" stroke="#fff" stroke-width="1.3"/></svg></span>
  </article>
  <article class="trip-card" style="left:376px;top:806px;height:318px;background:linear-gradient(180deg,#7f9a6a,#8b7a5c 55%,#3f3a31)" role="img" aria-label="Photo of a family smiling together on a forest trail">
    <div class="cap"><b>Family Trips</b><span>Bonding &amp; Adventure</span></div>
    <span class="go"><svg width="10" height="10" viewBox="0 0 10 10"><path d="M2 8L8 2M3 2h5v5" fill="none" stroke="#fff" stroke-width="1.3"/></svg></span>
  </article>
  <article class="trip-card" style="left:612px;top:832px;height:318px;background:linear-gradient(180deg,#9fbfd4,#c17a55 45%,#8a6a57 75%,#4a4a4c)" role="img" aria-label="Photo of a traveler on an open desert road with red rock cliffs">
    <div class="cap"><b>Texas Road Trips</b><span>East Texas Van Rentals</span></div>
    <span class="go"><svg width="10" height="10" viewBox="0 0 10 10"><path d="M2 8L8 2M3 2h5v5" fill="none" stroke="#fff" stroke-width="1.3"/></svg></span>
  </article>
  <article class="trip-card" style="left:846px;top:806px;height:318px;background:linear-gradient(180deg,#4d8fc4,#9cc3da 45%,#d7c8a8 70%,#7d6c55)" role="img" aria-label="Photo of a family walking on a beach under a blue sky">
    <div class="cap"><b>Other Destinations</b><span>Beaches, Mountains...</span></div>
    <span class="go"><svg width="10" height="10" viewBox="0 0 10 10"><path d="M2 8L8 2M3 2h5v5" fill="none" stroke="#fff" stroke-width="1.3"/></svg></span>
  </article>
</section>

<!-- Texas getaways -->
<section>
  <div class="photo" style="left:0;top:1224px;width:864px;height:486px;border-bottom-right-radius:160px;background:linear-gradient(160deg,#5e9bc9 0%,#a9cde0 30%,#3aa3a4 48%,#d9c8a8 70%,#c06b3a 100%)" role="img" aria-label="Photo of a woman in a sun hat relaxing on striped beach chairs by a tropical bay"></div>
  <div class="texas-panel">
    <div class="script">Begin Your Adventure</div>
    <h2>Best Texas<br>Getaways for Families</h2>
    <p>From Bayou Science Center to San Antonio river walks create memories that last a lifetime.</p>
    <span class="pill">See Family Packages <span class="arrow"><svg width="16" height="10" viewBox="0 0 16 10"><path d="M1 5h13M10 1l4 4-4 4" fill="none" stroke="#c4904a" stroke-width="1.6"/></svg></span></span>
  </div>
</section>

<!-- About -->
<section>
  <div class="about-copy">
    <div class="script">About</div>
    <h2>Roam Together<br>Travel Co.</h2>
    <div class="rule"></div>
    <p>We assist families with planning trips, organizing itineraries, and selecting destinations that fit their needs. From Brimwell magic to Texas road adventures, let's craft memories that last a lifetime.</p>
    <p>We don't just book trips — we craft story-filled journeys. With deep local partnerships and expert knowledge of family-friendly destinations, every detail is designed to reduce stress and increase wonder. From Brimwell magic to Texas open roads, your next chapter starts here.</p>
    <span class="pill">Read More <span class="arrow"><svg width="16" height="10" viewBox="0 0 16 10"><path d="M1 5h13M10 1l4 4-4 4" fill="none" stroke="#c4904a" stroke-width="1.6"/></svg></span></span>
  </div>
  <div class="photo" style="left:582px;top:1798px;width:442px;height:428px;border-radius:90px 20px 20px 20px;background:linear-gradient(180deg,#9fc6df 0%,#cfe0e8 45%,#ece6dc 70%,#d9cbb7 100%)" role="img" aria-label="Photo of parents and a young daughter playing together on a sandy beach"></div>
  <div class="badge"><b>15+</b><span>YEARS OF<br>EXPERIENCE</span></div>
</section>

<!-- Why choose us -->
<section class="why" role="img" aria-label="Backdrop photo of misty green mountain peaks">
  <div class="section-head" style="top:36px">
    <div class="script">Whist</div>
    <h2>Why Choose Us</h2>
    <div class="rule"></div>
    <p>Locally owned, personally crafted — we turn vacations into stories.</p>
  </div>
  <div class="feature" style="left:137px;top:167px"><div class="disc">
    <svg width="46" height="42" viewBox="0 0 46 42"><path d="M3 12l12-5 16 5 12-5v28l-12 5-16-5-12 5z" fill="none" stroke="#1d5862" stroke-width="2.4"/><circle cx="23" cy="12" r="6" fill="#c4904a"/></svg>Local<br>Expertise</div></div>
  <div class="feature" style="left:425px;top:167px"><div class="disc">
    <svg width="46" height="42" viewBox="0 0 46 42"><path d="M16 2h14l4 4v10c0 6-6 10-11 12-5-2-11-6-11-12V6z" fill="#c4904a"/><path d="M2 28l10-6 10 6 10-6 12 8-12 10-10-6-10 6z" fill="#1d5862"/></svg>Trusted<br>Partners</div></div>
  <div class="feature" style="left:713px;top:167px"><div class="disc">
    <svg width="46" height="42" viewBox="0 0 46 42"><path d="M20 2h6v38h-6z" fill="#1d5862"/><path d="M26 6h14l4 5-4 5H26z" fill="#1d5862"/><path d="M20 16H8l-4 5 4 5h12z" fill="#1d5862"/></svg>Texas<br>Road Trips</div></div>
  <div class="feature" style="left:281px;top:327px"><div class="disc">
    <svg width="46" height="42" viewBox="0 0 46 42"><rect x="6" y="4" width="24" height="34" rx="2" fill="none" stroke="#1d5862" stroke-width="2.4"/><path d="M11 14h14M11 20h14M11 26h10" stroke="#1d5862" stroke-width="2"/><path d="M28 30l16-6-4 6 4 6z" fill="#c4904a"/></svg>Personalized<br>Planning</div></div>
  <div class="feature" style="left:569px;top:327px"><div class="disc">
    <svg width="46" height="42" viewBox="0 0 46 42"><circle cx="15" cy="9" r="6" fill="#1d5862"/><circle cx="31" cy="9" r="6" fill="#1d5862"/><path d="M4 30c0-8 5-12 11-12s11 4 11 12z" fill="#1d5862"/><path d="M20 30c0-8 5-12 11-12s11 4 11 12z" fill="#1d5862"/><circle cx="23" cy="26" r="4" fill="#c4904a"/><path d="M16 40c0-6 3-8 7-8s7 2 7 8z" fill="#c4904a"/></svg>100%<br>Family Focus</div></div>
  <div class="feature" style="left:857px;top:327px"><div class="disc">
    <svg width="46" height="42" viewBox="0 0 46 42"><path d="M21 2h4v8h-4z" fill="#c4904a"/><rect x="14" y="10" width="18" height="10" fill="#1d5862"/><path d="M4 22h38l-6 12H10z" fill="#1d5862"/><path d="M2 38c6-3 10 3 14 0s10 3 14 0 10 3 14 0" fill="none" stroke="#c4904a" stroke-width="2"/></svg>Harbor &amp;<br>Cruise Expert</div></div>
</section>

<!-- Testimonials -->
<section class="abs" style="left:0;top:3090px;width:1200px;height:560px;overflow:hidden">
  <div class="section-head" style="top:30px">
    <div class="script">Testimonials</div>
    <h2>What Our Clients Say</h2>
    <div class="rule"></div>
  </div>
  <div class="review" style="left:-84px;top:150px"><span class="q">“</span><div class="who"><span class="av" style="background:#2f9e5b">C</span><div><div class="name">Christopher Adams</div><div class="stars">★★★★★</div></div></div><p>“Lorem ipsum est simplement un texte factice utilisé dans l'industrie de l'imprimerie et de la composition. Lorem ipsum est le texter.”</p></div>
  <div class="review" style="left:264px;top:150px"><span class="q">“</span><div class="who"><span class="av" style="background:#2f9e5b">J</span><div><div class="name">James Anderson</div><div class="stars">★★★★★</div></div></div><p>“Lorem ipsum est simplement un texte factice utilisé dans l'industrie de l'imprimerie et de la composition. Lorem ipsum est le texter.”</p></div>
  <div class="review" style="left:614px;top:150px"><span class="q">“</span><div class="who"><span class="av" style="background:#6b3fd4">S</span><div><div class="name">Samuel Harris</div><div class="stars">★★★★★</div></div></div><p>“Lorem ipsum est simplement un texte factice utilisé dans l'industrie de l'imprimerie et de la composition. Lorem ipsum est le texter.”</p><span class="abs" style="right:20px;bottom:16px;width:16px;height:16px;border-radius:50%;border:2px solid #c4904a"></span></div>
  <div class="review" style="left:966px;top:150px"><span class="q">“</span><div class="who"><span class="av" style="background:#2b6fd6">A</span><div><div class="name">Alexandra Doe</div><div class="stars">★★★★★</div></div></div><p>“Lorem ipsum est simplement un texte factice utilisé dans l'industrie de l'imprimerie et de la composition. Lorem ipsum est le texter.”</p></div>
  <div class="review" style="left:-60px;top:336px"><span class="q">“</span><div class="who"><div><div class="name">Robert Turner</div><div class="stars">★★★★★</div></div></div><p>“Lorem ipsum est simplement un texte factice utilisé dans l'industrie de l'imprimerie et de la composition. Lorem ipsum est le texter.”</p></div>
  <div class="review" style="left:288px;top:336px"><span class="q">“</span><div class="who"><span class="av" style="background:#f0a42b">T</span><div><div class="name">Thomas Brooks</div><div class="stars">★★★★★</div></div></div><p>“Lorem ipsum est simplement un texte factice utilisé dans l'industrie de l'imprimerie et de la composition. Lorem ipsum est le texter.”</p></div>
  <div class="review" style="left:638px;top:336px"><span class="q">“</span><div class="who"><span class="av" style="background:#2f9e5b">M</span><div><div class="name">Michael Carter</div><div class="stars">★★★★★</div></div></div><p>“Lorem ipsum est simplement un texte factice utilisé dans l'industrie de l'imprimerie et de la composition. Lorem ipsum est le texter.”</p></div>
  <div class="review" style="left:986px;top:336px"><span class="q">“</span><div class="who"><span class="av" style="background:#2b6fd6">D</span><div><div class="name">David Thompson</div><div class="stars">★★★★★</div></div></div><p>“Lorem ipsum est simplement un texte factice utilisé dans l'industrie de l'imprimerie et de la composition. Lorem ipsum est le texter.”</p></div>
</section>
<div class="dots"><i></i><i></i><i class="on"></i><i></i><i></i><i></i></div>

<!-- General inquiry -->
<section class="inquiry">
  <div class="section-head" style="top:80px">
    <div class="script">General Inquiry</div>
    <h2>Ready To Wander? Let's Talk</h2>
    <div class="rule"></div>
  </div>
</section>
<form>
  <div class="field" style="left:292px;top:3944px;width:300px"><svg width="12" height="12" viewBox="0 0 12 12"><circle cx="6" cy="4" r="2.5" fill="none" stroke="#999"/><path d="M1 11c1-3 3-4 5-4s4 1 5 4" fill="none" stroke="#999"/></svg><span class="sep"></span>First Name</div>
  <div class="field" style="left:608px;top:3944px;width:300px"><svg width="12" height="12" viewBox="0 0 12 12"><circle cx="6" cy="4" r="2.5" fill="none" stroke="#999"/><path d="M1 11c1-3 3-4 5-4s4 1 5 4" fill="none" stroke="#999"/></svg><span class="sep"></span>Last Name</div>
  <div class="field" style="left:292px;top:4012px;width:300px"><svg width="12" height="12" viewBox="0 0 12 12"><rect x="1" y="2.5" width="10" height="7" fill="none" stroke="#999"/><path d="M1 3l5 4 5-4" fill="none" stroke="#999"/></svg><span class="sep"></span>Your Email</div>
  <div class="field" style="left:608px;top:4012px;width:300px"><svg width="12" height="12" viewBox="0 0 12 12"><path d="M2 1h3l1 3-2 1c1 2 2 3 3 3l1-2 3 1v3c-6 0-9-3-9-9z" fill="none" stroke="#999"/></svg><span class="sep"></span>Phone</div>
  <div class="field" style="left:292px;top:4082px;width:616px;height:106px;align-items:flex-start;padding-top:18px"><svg width="12" height="12" viewBox="0 0 12 12"><circle cx="6" cy="6" r="4.5" fill="none" stroke="#999"/></svg><span class="sep"></span>Your Message</div>
  <div class="submit">Submit Now</div>
</form>

<!-- Subscribe -->
<section>
  <div class="section-head" style="top:4400px">
    <div class="script">Subscribe Now</div>
    <h2>Subscribe For Latest Update<br>About Travelling</h2>
    <div class="rule"></div>
    <p style="color:var(--ink)">Latest Updates, Exclusive Content, And Special Offers? Subscribe To Our Newsletter!</p>
  </div>
  <div class="sub-box">
    <svg width="16" height="12" viewBox="0 0 16 12" style="margin-right:6px"><rect x="1" y="1" width="14" height="10" fill="none" stroke="#999"/><path d="M1 1l7 6 7-6" fill="none" stroke="#999"/></svg>Your Email
    <span class="pill">Subscribe <svg width="16" height="10" viewBox="0 0 16 10"><path d="M1 5h13M10 1l4 4-4 4" fill="none" stroke="#fff" stroke-width="1.6"/></svg></span>
  </div>
</section>

<!-- Footer -->
<footer class="footer">
  <div class="abs" style="left:140px;top:96px">
    <h4>Quick Links</h4>
    <ul><li>Home</li><li>Brimwell</li><li>Family Trips</li><li>Road Trips</li><li>Destinations</li><li>About Us</li><li>Contact Us</li></ul>
  </div>
  <div class="abs" style="left:330px;top:96px">
    <h4>Contact Details</h4>
    <div class="contact-row"><svg width="12" height="14" viewBox="0 0 12 14"><path d="M6 13C2 8 1 6 1 5a5 5 0 0110 0c0 1-1 3-5 8z" fill="#fff"/><circle cx="6" cy="5" r="2" fill="#163d44"/></svg><span>402 Bluebonnet Ln.<br>Cedar Hollow, TX 75012</span></div>
    <div class="contact-row"><svg width="12" height="12" viewBox="0 0 12 12"><path d="M2 1h3l1 3-2 1c1 2 2 3 3 3l1-2 3 1v3c-6 0-9-3-9-9z" fill="#fff"/></svg><span>Phone<br>555.018.2240</span></div>
    <div class="contact-row"><svg width="12" height="12" viewBox="0 0 12 12"><rect x="0.5" y="2" width="11" height="8" fill="#fff"/><path d="M1 2.5l5 4 5-4" fill="none" stroke="#163d44"/></svg><span>Email<br>hello@roamtogether.example</span></div>
  </div>
  <div class="abs social" style="left:618px;top:96px">
    <h4>Social Media</h4>
    <ul><li><span class="dot" style="background:var(--gold);border-color:var(--gold)"></span>Kinfeed</li><li><span class="dot"></span>Reelbox</li><li><span class="dot"></span>Worklink</li><li><span class="dot"></span>Snapgram</li></ul>
  </div>
  <div class="footer-brand">Roam<br>Together<br>Travel Co.</div>
  <div class="copy">© 2026 Roam Together Travel Co. All Rights Reserved.</div>
</footer>

</body>
</html>
```